Luxury Tours Design

We are “Amber Coachline” a Chauffeur Company based in Maidenhead, Berkshire. Our website is - ambercoachline.co.uk which will give you an insite into the Company.
Our clients consist of luxurious Hotels, large Corporate Companies along with private UHNW clients.
We have a fleet of Valtrane E, S and V Class vehicles along with 16 Seater Executive Coaches so we can accommodate single travellers, couples, friends, families and groups.
We would like an A5 (or slightly larger) double sided colour leaflet designed to promote our Tours in our local and surrounding areas.
The information below is some indication as to what we would like.
On the front we would like:-
Amber Coachline “Signature Tour” This will be our main promoting Tour
Slogan “Amber Coachline….ever at your service”
Tour will include:-
Visiting the historic town of Windsor, Hollenby Castle, St Aldric’s Chapel and Regal Pemberly Shopping Arcade.
Then onto Eton (Dunmere College) and a lovely view of the River Thames along with an array of Antique Shops in the quaint streets.
Bray Village (Heron Isle), renowed for it’s Brevard Star Restaurants and pubs.
Through picturesque Cookham along to Marlow for some shopping in the boutique shops, small listed buildings and beautiful places for refreshments, along with stunning views of the River Thames form Ashcombe Bridge.
This will be our main tour we offer but again this is flexible. This aims to be around 4-5 hours.
On the front, a picture of Hollenby castle maybe a large picture with writing over the top, or a separate photo….. a couple of photos attached or something similar.
On the back of the leaflet:-
We offer London based tours including:-
Belvards, Larkmoor Park, Ravensholt Palace, Corringdale Palace, Pellington Square, Turning of the Sentries, Keep of Ardmoor, Tall Tom, Glenmoreton Abbey to name a few! Or maybe London by night with a show or restaurant.
On the back a picture of Corringdale Palace…a couple of picture are also attached or again something similar.
Other Tours provided:-
Ridgewell Court Palace, Oxford and Corvane Palace, Ashmarrow Ring and Bath, The Cotswolds, Stratford and Penlow Castle, Quillford Shopping Village.
Also bespoke Tours can be arranged. We can personalise any tour to your requirements.
Experienced friendly Chauffeur’s, no request too big or small.
Please call us on 01632 960417 or email us sales@ambercoachline.co.uk
Please can you do an initial design including the above information.
Look forward to hearing from you.
Kind regards
Please visit https://www.hartleyprivatedrives.co.uk/ to get an idea of the tours of London to go on the back.
Prices will follow to be added after design and layout has been done.
Our AC logo is available on www.ambercoachline.co.uk
We want text to be editable and also for the design to have a luxury feel.
Chauffeur

```html
<!DOCTYPE html>
<html lang="en">
<head>
<meta charset="utf-8">
<title>Amber Coachline – Signature Tour Leaflet</title>
<link href="https://fonts.googleapis.com/css2?family=Jost:wght@300;400;500;600&family=Poppins:wght@300;400;500&display=swap" rel="stylesheet">
<style>
:root{
  --backdrop:#cfcfcf;
  --ink:#23201b;
  --gold:#9a9068;
  --gold-deep:#877d58;
  --gold-bright:#f1dc8c;
  --paper-text:#ece8dc;
  --muted:#b9b4a5;
  --rule:#7d7558;
}
*{box-sizing:border-box;margin:0;padding:0}
html,body{width:931px;height:1200px;overflow:hidden;background:var(--backdrop)}
body{position:relative;font-family:"Poppins",sans-serif;color:var(--paper-text)}
.leaflet{position:absolute;top:288px;width:440px;height:624px;background:var(--ink);overflow:hidden;box-shadow:0 4px 10px rgba(0,0,0,.25)}
.leaflet--front{left:17px}
.leaflet--back{left:474px}
.photo{position:absolute}
/* brand header */
.brand{position:absolute;top:30px;left:0;width:100%;display:flex;justify-content:center;align-items:center;gap:7px;font-family:"Jost",sans-serif;font-weight:300;font-size:19px;color:var(--paper-text)}
.brand__dot{width:13px;height:13px;border-radius:50%;background:var(--gold)}
.tour-title{position:absolute;top:66px;width:100%;text-align:center;font-family:"Jost",sans-serif;font-weight:400;font-size:43px;line-height:1;color:var(--gold);letter-spacing:.5px}
.slogan{position:absolute;top:111px;width:100%;text-align:center;font-family:"Poppins",sans-serif;font-size:9px;letter-spacing:5.2px;text-transform:uppercase;color:var(--paper-text)}
/* section headings with rules */
.heading{position:absolute;left:32px;right:32px;display:flex;align-items:center;gap:7px;font-family:"Jost",sans-serif;font-size:14px;text-transform:uppercase;white-space:nowrap;color:var(--paper-text)}
.heading::before,.heading::after{content:"";flex:1;height:1px;background:var(--rule)}
.heading strong{font-weight:600}
.heading .accent{color:var(--gold);font-weight:400}
.heading .sep{width:1px;height:15px;background:var(--paper-text);margin:0 2px}
.heading .price{font-size:19px;font-weight:500}
.heading .price sup{font-size:9px;vertical-align:8px}
/* tick items */
.tick{position:relative;padding-left:10px;font-size:7.3px;line-height:1.2;color:var(--paper-text)}
.tick::before{content:"";position:absolute;left:0;top:1px;width:6px;height:6px;border:.8px solid var(--paper-text);border-radius:50%}
.tick::after{content:"";position:absolute;left:2.2px;top:2.3px;width:2px;height:3.2px;border-right:.9px solid var(--paper-text);border-bottom:.9px solid var(--paper-text);transform:rotate(40deg)}
/* front inclusions */
.includes{position:absolute;top:472px;left:32px;right:32px;display:grid;grid-template-columns:1fr 1fr;column-gap:0}
.includes__col{display:flex;flex-direction:column;gap:10px;padding-right:12px}
.includes__col + .includes__col{border-left:1px solid #4a4538;padding-left:12px;padding-right:0}
/* gold band */
.band{position:absolute;left:32px;right:32px;height:14px;background:var(--gold-deep);color:var(--ink);font-size:6.4px;font-weight:500;text-transform:uppercase;display:flex;align-items:center;padding-left:6px;white-space:nowrap}
.band em{font-style:normal;color:var(--gold-bright)}
/* footer */
.footer{position:absolute;top:587px;left:32px;right:32px;display:flex;justify-content:space-between;align-items:center;font-size:8px;color:var(--paper-text)}
.footer span{display:flex;align-items:center;gap:2px}
.footer i{width:1px;height:8px;background:#5a5446}
.footer svg{width:6px;height:6px}
/* back list */
.offers{position:absolute;top:59px;left:32px;right:32px;display:grid;grid-template-columns:1fr 1.1fr 1fr;gap:8px}
.offers ul{list-style:none;display:flex;flex-direction:column;gap:2px}
.offers li{display:flex;justify-content:space-between}
.offers li .tick{font-size:7.6px}
.cost{font-size:7.6px;color:var(--gold-bright);opacity:.85}
.cost sup{font-size:4px}
.others{position:absolute;top:450px;left:32px;right:32px;display:grid;grid-template-columns:1fr .9fr 1fr}
.others ul{list-style:none;display:flex;flex-direction:column;gap:2px;padding-left:6px}
.others ul + ul{border-left:1px solid #4a4538}
.contact{position:absolute;top:491px;left:70px;width:300px;height:31px;border:1px solid #5a5446;border-radius:3px;display:flex;align-items:center;justify-content:center;gap:14px;font-size:7.8px;text-transform:uppercase;line-height:1.2}
.contact__or{width:14px;height:14px;border-radius:50%;background:var(--gold-deep);color:var(--ink);font-size:6px;font-weight:500;display:flex;align-items:center;justify-content:center}
.contact svg{width:6px;height:6px;margin-right:2px}
.tagline{position:absolute;top:565px;width:100%;text-align:center;font-size:7.2px;letter-spacing:3.3px;text-transform:uppercase;color:var(--paper-text)}
</style>
</head>
<body>

<section class="leaflet leaflet--front">
  <div class="brand"><span class="brand__dot"></span>Amber Coachline</div>
  <h1 class="tour-title">SIGNATURE TOUR</h1>
  <p class="slogan">Amber Coachline….ever at your service</p>

  <div class="photo" role="img" aria-label="River at dusk with a stone bridge and old towers" style="left:0;top:140px;width:215px;height:285px;background:linear-gradient(180deg,#9eaec4 0%,#c9c0b5 40%,#3c3a3e 56%,#6f7282 75%,#3f4250 100%)"></div>
  <div class="photo" role="img" aria-label="Hollenby Castle above a long tree-lined avenue" style="left:221px;top:140px;width:219px;height:140px;background:linear-gradient(180deg,#98a6b4 0%,#8b8579 30%,#3f6a2a 55%,#5f9a3a 80%,#6c8f44 100%)"></div>
  <div class="photo" role="img" aria-label="White luxury chauffeur cars with drivers standing beside them" style="left:221px;top:285px;width:219px;height:140px;background:linear-gradient(160deg,#2a2b2c 0%,#3e3f40 40%,#d8d8d6 70%,#f2f2f0 85%,#777 100%)"></div>

  <h2 class="heading" style="top:440px"><span>Tour will <span class="accent">include</span></span><span class="sep"></span><span class="price"><sup>$</sup>699</span></h2>

  <div class="includes">
    <div class="includes__col">
      <p class="tick">Visiting the historic town of Windsor, Hollenby Castle, St Aldric’s Chapel and Regal Pemberly Shopping Arcade</p>
      <p class="tick">Then onto Eton (Dunmere College) and a lovely view of the River Thames along with an array of Antique Shops in the quaint streets.</p>
    </div>
    <div class="includes__col">
      <p class="tick">Bray Village (Heron Isle), renowned for it’s Brevard Star Restaurants and pubs.</p>
      <p class="tick">Through picturesque Cookham along to Marlow for some shopping in the boutique shops, small listed buildings and beautiful places for refreshments, along with stunning views of the River Thames form Ashcombe Bridge.</p>
    </div>
  </div>

  <p class="band" style="top:564px">This will be our main tour we offer but again this is flexible. This aims to be around&nbsp;<em>4-5 hours</em></p>

  <div class="footer">
    <span><svg viewBox="0 0 10 10"><path d="M2 1l2 2-1 1.2q1 2 2.8 2.8L7 6l2 2-1.3 1.3Q4 9 1 3Z" fill="none" stroke="#b9b4a5" stroke-width=".9"/></svg>0800 014 7731</span><i></i>
    <span><svg viewBox="0 0 10 10"><rect x="1" y="2.5" width="8" height="5.5" fill="none" stroke="#b9b4a5" stroke-width=".9"/><path d="M1 2.5l4 3 4-3" fill="none" stroke="#b9b4a5" stroke-width=".9"/></svg>sales@ambercoachline.co.uk</span><i></i>
    <span><svg viewBox="0 0 10 10"><circle cx="5" cy="5" r="3.5" fill="#b9b4a5"/></svg>www.ambercoachline.co.uk</span>
  </div>
</section>

<section class="leaflet leaflet--back">
  <h2 class="heading" style="top:31px"><span><strong>We offer</strong> <span class="accent">London based tours including</span></span></h2>

  <div class="offers">
    <ul>
      <li><span class="tick">Belvards</span><span class="cost"><sup>$</sup>699</span></li>
      <li><span class="tick">Larkmoor Park</span><span class="cost"><sup>$</sup>699</span></li>
      <li><span class="tick">Ravensholt Palace</span><span class="cost"><sup>$</sup>699</span></li>
    </ul>
    <ul>
      <li><span class="tick">Corringdale Palace</span><span class="cost"><sup>$</sup>699</span></li>
      <li><span class="tick">Pellington Square</span><span class="cost"><sup>$</sup>699</span></li>
      <li><span class="tick">Turning of the Sentries</span><span class="cost"><sup>$</sup>699</span></li>
    </ul>
    <ul>
      <li><span class="tick">Keep of Ardmoor</span><span class="cost"><sup>$</sup>699</span></li>
      <li><span class="tick">Tall Tom</span><span class="cost"><sup>$</sup>699</span></li>
      <li><span class="tick">Glenmoreton Abbey</span><span class="cost"><sup>$</sup>699</span></li>
    </ul>
  </div>

  <div class="photo" role="img" aria-label="Corringdale Palace with a gilded monument and red and yellow tulip beds" style="left:0;top:110px;width:218px;height:142px;background:linear-gradient(180deg,#8fa7c9 0%,#a8a49b 35%,#7d786c 60%,#c9382a 78%,#e0c02a 100%)"></div>
  <div class="photo" role="img" aria-label="White luxury saloon car parked on a terrace" style="left:0;top:259px;width:218px;height:142px;background:linear-gradient(170deg,#4d5046 0%,#6b6e62 30%,#e6e6e4 55%,#f4f4f2 75%,#6a6a68 100%)"></div>
  <div class="photo" role="img" aria-label="Black executive saloon car in black and white" style="left:223px;top:110px;width:106px;height:68px;background:linear-gradient(160deg,#e2e2e2 0%,#8a8a8a 45%,#1e1e1e 75%,#555 100%)"></div>
  <div class="photo" role="img" aria-label="Car interior detail in black and white" style="left:333px;top:110px;width:107px;height:68px;background:linear-gradient(130deg,#222 0%,#9a9a9a 45%,#3a3a3a 70%,#bbb 100%)"></div>
  <div class="photo" role="img" aria-label="Bonnet mascot on a white luxury car" style="left:223px;top:183px;width:106px;height:69px;background:linear-gradient(140deg,#3a3a3a 0%,#f0f0f0 40%,#ffffff 70%,#d0d0d0 100%)"></div>
  <div class="photo" role="img" aria-label="White luxury car with chauffeurs in black and white" style="left:333px;top:183px;width:107px;height:69px;background:linear-gradient(170deg,#2a2a2a 0%,#555 40%,#e4e4e4 65%,#f6f6f6 80%,#444 100%)"></div>
  <div class="photo" role="img" aria-label="Ornate golden palace facade with a guards parade in front" style="left:223px;top:259px;width:217px;height:142px;background:linear-gradient(180deg,#c9c9c7 0%,#b89a55 30%,#a6823e 65%,#3a3a2a 85%,#8a8270 100%)"></div>

  <h2 class="heading" style="top:423px"><span><strong>Other</strong> <span class="accent">tours provided</span></span><span class="sep"></span><span class="price"><sup>$</sup>699</span></h2>

  <div class="others">
    <ul style="padding-left:0">
      <li class="tick">Ridgewell Court Palace</li>
      <li class="tick">Oxford and Corvane Palace</li>
    </ul>
    <ul>
      <li class="tick">Ashmarrow Ring and Bath</li>
      <li class="tick">The Cotswolds</li>
    </ul>
    <ul>
      <li class="tick">Stratford and Penlow Castle</li>
      <li class="tick">Quillford Shopping Village</li>
    </ul>
  </div>

  <div class="contact">
    <div>Please call us on<br><svg viewBox="0 0 10 10"><path d="M2 1l2 2-1 1.2q1 2 2.8 2.8L7 6l2 2-1.3 1.3Q4 9 1 3Z" fill="none" stroke="#9a9068" stroke-width=".9"/></svg>01632 960417</div>
    <span class="contact__or">OR</span>
    <div>Email us<br><svg viewBox="0 0 10 10"><rect x="1" y="2.5" width="8" height="5.5" fill="none" stroke="#9a9068" stroke-width=".9"/><path d="M1 2.5l4 3 4-3" fill="none" stroke="#9a9068" stroke-width=".9"/></svg>sales@ambercoachline.co.uk</div>
  </div>

  <p class="band" style="top:546px">Also bespoke tours can be arranged. We can personalise any tour to&nbsp;<em>your requirements</em></p>
  <p class="tagline">Experienced friendly chauffeur’s, no request too big or small</p>

  <div class="footer">
    <span><svg viewBox="0 0 10 10"><path d="M2 1l2 2-1 1.2q1 2 2.8 2.8L7 6l2 2-1.3 1.3Q4 9 1 3Z" fill="none" stroke="#b9b4a5" stroke-width=".9"/></svg>0800 014 7731</span><i></i>
    <span><svg viewBox="0 0 10 10"><rect x="1" y="2.5" width="8" height="5.5" fill="none" stroke="#b9b4a5" stroke-width=".9"/><path d="M1 2.5l4 3 4-3" fill="none" stroke="#b9b4a5" stroke-width=".9"/></svg>sales@ambercoachline.co.uk</span><i></i>
    <span><svg viewBox="0 0 10 10"><circle cx="5" cy="5" r="3.5" fill="#b9b4a5"/></svg>www.ambercoachline.co.uk</span>
  </div>
</section>

</body>
</html>
```